Business Card Design

We need a business card designed for our new company. Prefer a black card with white logo & writing.

Contact Information for Business Card

Ted Galloway, address: 7-4812 Fernhollow Road, Abbotsford, BC, V3K 8R2, Office Phone: 604-712-3390, Cell: 604-947-2164, Email: ted@resinworkshub.ca

Colors

Designer to choose only greyscale colors for use in the design.

```html
<!DOCTYPE html>
<html lang="en">
<head>
<meta charset="utf-8">
<title>Resinworks Hub – Business Card</title>
<link href="https://fonts.googleapis.com/css2?family=Poppins:wght@300;400;500;700&display=swap" rel="stylesheet">
<style>
  :root {
    --stage: #1e1e20;
    --card: #232326;
    --card-edge: #2e2e32;
    --ink: #ffffff;
    --ink-soft: #d9d9d9;
    --band-ink: #1c1c1e;
    --grey-mid: #8a8a8f;
    --grey-dark: #5c5c61;
  }
  * { box-sizing: border-box; margin: 0; padding: 0; }
  html, body {
    width: 1200px; height: 711px; overflow: hidden;
    background: var(--stage);
    font-family: "Poppins", sans-serif;
  }
  .canvas { position: relative; width: 1200px; height: 711px; }

  .card {
    position: absolute;
    width: 540px; height: 309px;
    background: var(--card);
    border: 1px solid var(--card-edge);
    border-radius: 4px;
    overflow: hidden;
  }
  .card--front { left: 40px; top: 201px; }
  .card--back  { left: 620px; top: 201px; }

  /* Front */
  .front-texture {
    position: absolute; inset: 0;
    background: radial-gradient(ellipse at 60% 30%, #2c2c30 0%, #222225 60%, #1d1d20 100%);
  }
  .brand {
    position: absolute;
    display: flex; align-items: center; gap: 10px;
    color: var(--ink);
    font-weight: 700;
    text-transform: uppercase;
    letter-spacing: 1px;
    white-space: nowrap;
  }
  .brand__mark { background: var(--ink); flex: none; }
  .card--front .brand {
    left: 50%; top: 50%; transform: translate(-50%, -50%);
    font-size: 40px;
  }
  .card--front .brand__mark { width: 30px; height: 30px; }

  /* Back */
  .card--back .brand {
    left: 30px; top: 122px;
    font-size: 19px;
    gap: 8px;
  }
  .card--back .brand__mark { width: 16px; height: 16px; }

  .divider {
    position: absolute; left: 0; top: 0; width: 540px; height: 309px;
  }
  .divider line { stroke: var(--grey-mid); stroke-width: 1; }

  .person {
    position: absolute; left: 332px; top: 42px;
    color: var(--ink);
  }
  .person__name { font-size: 26px; line-height: 1.05; font-weight: 300; white-space: nowrap; }
  .person__name strong { font-weight: 700; }
  .person__role { font-size: 12.5px; font-weight: 300; color: var(--ink-soft); margin-top: 2px; }

  .contacts { list-style: none; margin-top: 14px; }
  .contacts li {
    display: flex; align-items: center; gap: 9px;
    font-size: 13px; font-weight: 300; color: var(--ink);
    line-height: 21px; white-space: nowrap;
  }
  .contacts svg { width: 12px; height: 12px; flex: none; fill: none; stroke: var(--ink); stroke-width: 1.6; }

  .address-band {
    position: absolute; left: 0; bottom: 46px;
    width: 430px; height: 30px;
    background: var(--ink);
    clip-path: polygon(0 0, 100% 0, 94% 50%, 100% 100%, 0 100%);
    display: flex; align-items: center;
    padding-left: 44px;
    color: var(--band-ink);
    font-size: 13px; font-weight: 500;
    white-space: nowrap;
  }
  .layers {
    position: absolute; right: 18px; bottom: 56px;
    width: 100px; height: 60px;
    background: linear-gradient(135deg, var(--ink) 0%, var(--grey-mid) 55%, var(--grey-dark) 100%);
    clip-path: polygon(0 55%, 45% 20%, 100% 0, 80% 45%, 40% 100%);
    opacity: .9;
  }
</style>
</head>
<body>
<main class="canvas">

  <section class="card card--front" aria-label="Card front">
    <div class="front-texture" role="img" aria-label="Repeating tone-on-tone brand pattern"></div>
    <div class="brand"><span class="brand__mark"></span>Resinworks Hub</div>
  </section>

  <section class="card card--back" aria-label="Card back">
    <div class="brand"><span class="brand__mark"></span>Resinworks Hub</div>

    <svg class="divider" viewBox="0 0 540 309" aria-hidden="true">
      <line x1="290" y1="45" x2="318" y2="215"/>
    </svg>

    <div class="person">
      <h1 class="person__name"><strong>Ted</strong> Galloway</h1>
      <p class="person__role">Founder &amp; CEO</p>
      <ul class="contacts">
        <li>
          <svg viewBox="0 0 24 24"><path d="M5 3l4 1 1 5-2 2a12 12 0 0 0 5 5l2-2 5 1 1 4-3 2C10 21 3 14 3 6z"/></svg>
          604-712-3390
        </li>
        <li>
          <svg viewBox="0 0 24 24"><rect x="6" y="2" width="12" height="20" rx="2"/><line x1="11" y1="18" x2="13" y2="18"/></svg>
          604-947-2164
        </li>
        <li>
          <svg viewBox="0 0 24 24"><circle cx="12" cy="12" r="9"/><path d="M3 12h18M12 3c3 3 3 15 0 18M12 3c-3 3-3 15 0 18"/></svg>
          www.resinworkshub.ca
        </li>
        <li>
          <svg viewBox="0 0 24 24"><rect x="3" y="6" width="18" height="13" rx="1"/><path d="M3 7l9 7 9-7"/></svg>
          ted@resinworkshub.ca
        </li>
      </ul>
    </div>

    <div class="address-band">7-4812 Fernhollow Road, Abbotsford, BC, V3K 8R2.</div>
    <div class="layers" role="img" aria-label="Stacked floor-layer graphic in grey tones"></div>
  </section>

</main>
</body>
</html>
```